Birch Hauling Business Card Design Project

We need a new company business card. We provide professional timber harvesting (logging) and forest management services. I'm open to any creative design. Most company caps and shirts are navy blue and Light grey. Logo does not necessarily have to contain those colors. Logo containing picture of logging equipment, log truck, trees, or logs are acceptable. Be creative. Final logo should communicate our company's pride and professionalism in the East Texas Timber Industry.
Updates

Target Market(s)

Timber owners, sawmills, and forestry professionals

Industry/Entity Type

Business

Requirements
Must have
• Must have Contact Info.
Phone: 555-402-5917
address: PO Box 4830
Cedar Ridge, Tx 75012
www.jmbirchhauling.example
jmbirchhauling@mailbox.example
Owner: Jared Marsh

Or design must leave room for this info.

```html
<!DOCTYPE html>
<html lang="en">
<head>
<meta charset="utf-8">
<title>Birch Hauling Business Cards</title>
<link rel="stylesheet" href="https://fonts.googleapis.com/css2?family=Open+Sans:wght@400;600;700&display=swap">
<style>
  :root {
    --bg: #d9d9d9;
    --brown: #4a2317;
    --brown-dark: #2e0c06;
    --green: #8cbd4a;
    --white: #f1f1f1;
    --ink: #2a1a12;
  }
  * { margin: 0; padding: 0; box-sizing: border-box; }
  html, body { width: 1200px; height: 864px; overflow: hidden; }
  body {
    background: var(--bg);
    font-family: "Open Sans", Arial, sans-serif;
    display: flex;
    align-items: center;
    justify-content: center;
    gap: 40px;
  }
  .card {
    position: relative;
    width: 560px;
    height: 320px;
    background: var(--white);
    overflow: hidden;
    box-shadow: 0 6px 18px rgba(0,0,0,0.18);
  }
  .card-art { position: absolute; inset: 0; width: 100%; height: 100%; }
  .company {
    position: absolute;
    font-weight: 700;
    line-height: 1.15;
    font-size: 27px;
  }
  .card-front .company { left: 38px; top: 38px; color: var(--green); }
  .owner-name {
    position: absolute;
    left: 38px; top: 128px;
    font-size: 20px;
    font-weight: 600;
    color: #ffffff;
    text-transform: uppercase;
    letter-spacing: 0.5px;
  }
  .owner-role {
    position: absolute;
    left: 38px; top: 155px;
    font-size: 12px;
    font-weight: 600;
    color: var(--green);
  }
  .contact {
    position: absolute;
    left: 300px; top: 226px;
    list-style: none;
    font-size: 13px;
    color: var(--ink);
    line-height: 20px;
  }
  .contact li { display: flex; align-items: center; gap: 8px; white-space: nowrap; }
  .contact .icon { width: 12px; height: 12px; flex: none; }
  .contact .address { margin-left: -20px; }
  .card-back .company { left: 250px; top: 200px; color: var(--brown-dark); }
</style>
</head>
<body>

  <section class="card card-front">
    <svg class="card-art" viewBox="0 0 350 200" preserveAspectRatio="none" aria-hidden="true">
      <defs>
        <linearGradient id="front-green" x1="0" y1="1" x2="1" y2="0">
          <stop offset="0" stop-color="#a7cf68"/>
          <stop offset="1" stop-color="#7fb23c"/>
        </linearGradient>
      </defs>
      <path d="M0,0 H262 C235,115 125,172 0,186 Z" fill="var(--brown)"/>
      <path d="M0,200 V194 C100,190 200,150 350,20 V200 Z" fill="url(#front-green)"/>
    </svg>
    <div class="company">J.M. Birch<br>Hauling Company</div>
    <div class="owner-name">Jared Marsh</div>
    <div class="owner-role">Owner</div>
    <ul class="contact">
      <li>
        <svg class="icon" viewBox="0 0 12 12" aria-hidden="true"><circle cx="6" cy="3.5" r="2.6" fill="#fff"/><path d="M1,12 C1,7.5 11,7.5 11,12 Z" fill="#fff"/></svg>
        555-402-5917
      </li>
      <li>
        <svg class="icon" viewBox="0 0 12 12" aria-hidden="true"><circle cx="6" cy="6" r="5" fill="none" stroke="#fff" stroke-width="1.3"/><ellipse cx="6" cy="6" rx="2.2" ry="5" fill="none" stroke="#fff" stroke-width="1"/><line x1="1" y1="6" x2="11" y2="6" stroke="#fff" stroke-width="1"/></svg>
        www.jmbirchhauling.example
      </li>
      <li>
        <svg class="icon" viewBox="0 0 12 12" aria-hidden="true"><rect x="0.5" y="2" width="11" height="8" fill="#fff"/><path d="M0.5,2 L6,6.5 L11.5,2" fill="none" stroke="var(--green)" stroke-width="1"/></svg>
        jmbirchhauling@mailbox.example
      </li>
      <li class="address">PO Box 4830 Cedar Ridge, Tx 75012</li>
    </ul>
  </section>

  <section class="card card-back">
    <svg class="card-art" viewBox="0 0 350 200" preserveAspectRatio="none" aria-hidden="true">
      <defs>
        <linearGradient id="back-green" x1="0" y1="0" x2="1" y2="1">
          <stop offset="0" stop-color="#8fc04a"/>
          <stop offset="1" stop-color="#a4cd62"/>
        </linearGradient>
      </defs>
      <path d="M0,0 H350 V10 C250,18 90,58 0,118 Z" fill="url(#back-green)"/>
      <path d="M0,130 C95,70 240,30 345,24 C240,42 125,95 80,200 H0 Z" fill="var(--brown-dark)"/>
    </svg>
    <div class="company">J.M. Birch<br>Hauling Company</div>
  </section>

</body>
</html>
```